THE WELLNESS BARN WEBSITE for Physio, Fitness, health

An attractive website advertising a physiotherapyand fitness / gym business, not generic, colours are natural, greens, browns, beiges. No cheesy pictures. With the ability to sell a small,amount of goods online if i decide to. Simple to navigate. Text boxes that i can input the main information and change easily. Somewhere to put my timetable. Easy to find contact details. However many pages it needs, im not fussed.
Target Market(s)
People looking for rehabilitation or fitness classes
Industry/Entity Type
Physiotherapy, Fitness, Gym, Health
Coding
Coded - Design and coding required
Number of Pages Required
1 page
Font styles to use
Other font styles liked:
- Im not fusse,ld, not script
Requirements
Must have
- Will upload posts from my business insta page for reference about the feel. Earthy natural tones, I have a lot of timber, and rustic looking piece's, plants etc in my clinic
Nice to have
- Simple to navigate
Should not have
- Cheesy "yoga" or generic "people doing physio" pics

```html
<!DOCTYPE html>
<html lang="en">
<head>
<meta charset="utf-8">
<title>The Wellness Barn</title>
<link href="https://fonts.googleapis.com/css2?family=Oswald:wght@500;600;700&family=Poppins:wght@400;500;600&display=swap" rel="stylesheet">
<style>
:root{
  --green-dark:#34421f;
  --green:#7b8759;
  --beige:#e6d7b3;
  --beige-light:#efe3c6;
  --brown:#8a6a36;
  --ink:#2d2a22;
  --line:#b9a77f;
  --white:#ffffff;
}
*{box-sizing:border-box;margin:0;padding:0}
html,body{width:1200px;height:4876px;overflow:hidden}
body{font-family:'Poppins',sans-serif;color:var(--ink);background:var(--beige);position:relative}
.section{position:absolute;left:0;width:1200px}
.center{text-align:center}
.eyebrow{font-family:'Oswald',sans-serif;font-weight:600;font-size:20px;letter-spacing:1px;color:var(--green-dark)}
.heading{font-family:'Oswald',sans-serif;font-weight:700;font-size:46px;line-height:1.1;color:var(--green-dark);text-transform:uppercase}
.rule{width:90px;height:3px;background:var(--green-dark);margin:14px auto 0}
.on-green .eyebrow,.on-green .heading{color:var(--white)}
.on-green .rule{background:var(--white)}
.btn{display:inline-block;background:var(--brown);color:var(--white);font-family:'Poppins',sans-serif;font-weight:600;font-size:15px;padding:14px 26px;border-radius:3px;letter-spacing:.5px}
.placeholder{position:absolute}
.hero{top:0;height:600px}
.hero-photo{left:0;top:0;width:1200px;height:600px;background:linear-gradient(180deg,#5e5a52 0%,#3f3d38 55%,#8c8170 100%)}
.logo{position:absolute;left:26px;top:14px;display:flex;align-items:center;gap:10px}
.logo-dot{width:22px;height:22px;border-radius:50%;background:var(--green)}
.logo-name{font-family:'Oswald',sans-serif;font-weight:700;font-size:28px;color:var(--white);line-height:1}
.hero .trial{position:absolute;left:594px;top:8px;padding:10px 20px;font-size:13px}
.contact-top{position:absolute;left:790px;top:6px;display:flex;gap:10px;align-items:center;color:var(--white)}
.contact-top .ic{width:36px;height:36px;border-radius:50%;background:var(--brown);display:flex;align-items:center;justify-content:center}
.contact-top small{display:block;font-size:13px}
.contact-top b{font-size:17px}
.nav{position:absolute;left:458px;top:78px;display:flex;gap:34px}
.nav a{font-weight:600;font-size:15px;color:var(--white);text-decoration:none}
.welcome{top:600px;height:520px;background:linear-gradient(180deg,var(--beige-light),var(--beige))}
.welcome .eyebrow{padding-top:90px}
.welcome p{width:640px;margin:30px auto 0;font-size:15px;line-height:1.7}
.welcome .btn{margin-top:30px}
.plant{top:40px;width:180px;height:380px;background:linear-gradient(180deg,#6f8a45 0%,#7c9550 60%,#f2f0ea 61%,#dcd9d2 100%);border-radius:80px 80px 20px 20px}
.plant-left{left:30px}
.plant-right{right:30px}
.products{top:1100px;height:660px;background:var(--green)}
.products .eyebrow{padding-top:80px}
.cards{position:absolute;top:232px;left:112px;display:flex;gap:24px}
.card{width:228px;text-align:center;color:var(--white)}
.card-photo{width:228px;height:230px;border:6px solid var(--beige-light);background:linear-gradient(160deg,#a89574,#6d5f47)}
.card h4{font-weight:600;font-size:14px;margin-top:14px;text-transform:uppercase}
.card .price{font-size:15px;margin-top:4px}
.card p{font-size:13px;margin-top:6px;line-height:1.5}
.offer{top:1760px;height:680px;background:linear-gradient(180deg,var(--beige),var(--beige-light))}
.offer .eyebrow{padding-top:108px}
.services{position:absolute;top:250px;left:170px;display:flex;gap:60px}
.service{width:240px;text-align:center}
.service .icon{width:150px;height:150px;margin:0 auto;border-radius:50%;background:var(--brown);display:flex;align-items:center;justify-content:center}
.service h4{font-weight:600;font-size:15px;color:var(--green-dark);margin-top:28px;line-height:1.5;text-transform:uppercase}
.service p{font-size:13px;line-height:1.6;margin-top:12px}
.arrow{position:absolute;top:400px}
.testimonials{top:2440px;height:600px;background:var(--beige)}
.testimonials .eyebrow{padding-top:130px}
.quote{position:absolute;background:var(--beige-light);border-radius:8px;padding:22px;box-shadow:0 6px 18px rgba(60,50,30,.15);text-align:left}
.quote.featured{background:var(--white)}
.quote .who{display:flex;align-items:center;gap:14px}
.avatar{width:56px;height:56px;border-radius:50%;background:linear-gradient(160deg,#b69a7a,#6b5440)}
.quote b{font-weight:600;font-size:14px;display:block;text-transform:uppercase}
.quote small{font-size:12px;color:#6c6553}
.quote p{font-size:13px;line-height:1.6;margin-top:14px}
.team{top:3040px;height:580px;background:var(--green)}
.team .eyebrow{padding-top:120px}
.team-photo{left:220px;top:260px;width:300px;height:300px;border-radius:50%;background:linear-gradient(160deg,#e9e5de,#a49a8e)}
.member{position:absolute;left:620px;top:300px;color:var(--white);width:360px;text-align:left}
.member h3{font-family:'Oswald',sans-serif;font-weight:500;font-size:28px;text-transform:uppercase}
.member small{font-size:13px}
.member p{font-size:13px;line-height:1.6;margin-top:18px}
.member .btn{margin-top:26px}
.faq{top:3620px;height:680px;background:linear-gradient(180deg,var(--beige-light),var(--beige))}
.faq .eyebrow{padding-top:100px}
.faq .intro{width:620px;margin:28px auto 0;font-size:15px;line-height:1.7}
.faq-list{width:760px;margin:36px auto 0}
.faq-item{display:flex;justify-content:space-between;border-bottom:1px solid var(--line);padding:18px 0;font-weight:500;font-size:15px;text-align:left}
.faq .btn{margin-top:34px}
.footer{top:4300px;height:576px;background:var(--beige)}
.footer .logo{position:static;justify-content:center;padding-top:60px}
.footer .logo-name{color:var(--green-dark);font-size:40px}
.footer-nav{display:flex;justify-content:center;gap:36px;margin-top:40px}
.footer-nav a{font-weight:600;font-size:15px;color:var(--ink);text-decoration:none}
.cols{display:flex;justify-content:center;gap:60px;margin-top:36px}
.col{width:270px;text-align:center;font-size:13px;line-height:1.6}
.col h5{font-weight:600;font-size:14px;margin-bottom:8px}
.copy{position:absolute;top:508px;left:0;width:1200px;border-top:1px solid var(--line);padding-top:18px;text-align:center;font-size:13px}
.edge{position:absolute;left:0;width:1200px}
</style>
</head>
<body>

<header class="section hero">
  <div class="placeholder hero-photo" role="img" aria-label="Group photo of class members celebrating in the gym"></div>
  <div class="logo"><span class="logo-dot"></span><span class="logo-name">THE WELLNESS BARN</span></div>
  <span class="btn trial">GET A FREE TRIAL</span>
  <div class="contact-top">
    <span class="ic"><svg width="18" height="14" viewBox="0 0 18 14"><rect x="1" y="1" width="16" height="12" fill="none" stroke="#fff" stroke-width="1.6"/><path d="M1 1l8 7 8-7" fill="none" stroke="#fff" stroke-width="1.6"/></svg></span>
    <div><small>Email Us</small><b>hello@wellnessbarn.example</b></div>
  </div>
  <nav class="nav"><a>HOME</a><a>SHOP</a><a>ABOUT US</a><a>PROGRAMS</a><a>TESTIMONIALS</a><a>CONTACT US</a></nav>
</header>

<section class="section welcome center">
  <div class="placeholder plant plant-left" role="img" aria-label="Potted leafy plant in white pot"></div>
  <div class="placeholder plant plant-right" role="img" aria-label="Potted leafy plant in white pot"></div>
  <div class="eyebrow">WELCOME TO</div>
  <h1 class="heading">THE WELLNESS BARN</h1>
  <div class="rule"></div>
  <p>Discover a healthier you with our Physiotherapist-led programs. At The Wellness Barn Greenvale, we focus on safe and effective movement to enhance your quality of life. Join us for a comprehensive approach to wellbeing.</p>
  <span class="btn">GET A FREE TRIAL</span>
</section>

<section class="section products on-green center">
  <svg class="edge" style="top:-1px" height="30" viewBox="0 0 1200 30" preserveAspectRatio="none"><path d="M0 0H1200V12L1150 22 1100 10 1040 24 980 12 920 26 860 14 800 24 740 10 680 22 620 12 560 26 500 14 440 24 380 10 320 22 260 12 200 26 140 14 80 24 0 12Z" fill="#e6d7b3"/></svg>
  <div class="eyebrow">OUR SHOP</div>
  <h2 class="heading">OUR PRODUCTS</h2>
  <div class="rule"></div>
  <div class="cards">
    <div class="card"><div class="card-photo" role="img" aria-label="Wheat bags on a shelf"></div><h4>WHEAT BAGS</h4><div class="price">$ 100.00</div><p>Soft heat packs for easing sore muscles</p></div>
    <div class="card"><div class="card-photo" role="img" aria-label="Drink bottle"></div><h4>DRINK BOTTLES</h4><div class="price">$ 100.00</div><p>Sturdy drink bottle for every session</p></div>
    <div class="card"><div class="card-photo" role="img" aria-label="Body oil bottle among plants"></div><h4>BODY OIL</h4><div class="price">$ 100.00</div><p>Natural massage oil for tired muscles</p></div>
    <div class="card"><div class="card-photo" role="img" aria-label="Cap and accessories"></div><h4>ACCESSORIES</h4><div class="price">$ 100.00</div><p>Caps and gear for training in style</p></div>
  </div>
  <svg class="edge" style="bottom:-1px" height="30" viewBox="0 0 1200 30" preserveAspectRatio="none"><path d="M0 30H1200V16L1140 6 1080 18 1020 4 960 16 900 6 840 20 780 8 720 18 660 4 600 16 540 6 480 20 420 8 360 18 300 4 240 16 180 6 120 20 60 8 0 16Z" fill="#e6d7b3"/></svg>
</section>

<section class="section offer center">
  <div class="eyebrow">WHAT WE DO</div>
  <h2 class="heading">WHAT WE OFFER</h2>
  <div class="rule"></div>
  <svg class="arrow" style="left:62px" width="20" height="20" viewBox="0 0 20 20"><path d="M14 3L6 10l8 7" fill="none" stroke="#34421f" stroke-width="3"/></svg>
  <svg class="arrow" style="left:1118px" width="20" height="20" viewBox="0 0 20 20"><path d="M6 3l8 7-8 7" fill="none" stroke="#34421f" stroke-width="3"/></svg>
  <div class="services">
    <div class="service"><div class="icon"><svg width="60" height="60" viewBox="0 0 60 60"><circle cx="30" cy="12" r="6" fill="#fff"/><rect x="24" y="22" width="12" height="30" rx="5" fill="#fff"/></svg></div><h4>PHYSIOTHERAPY CLASSES<br>FOR EVERYONE</h4><p>Our classes are tailored for all ages, focusing on safe movement to enhance mobility and overall health.</p></div>
    <div class="service"><div class="icon"><svg width="60" height="60" viewBox="0 0 60 60"><circle cx="30" cy="24" r="14" fill="none" stroke="#fff" stroke-width="4"/><path d="M16 50h28" stroke="#fff" stroke-width="4"/></svg></div><h4>HOLISTIC WELLNESS<br>PROGRAMS</h4><p>Our programs integrate physical activity with nutritional guidance to support sustainable health improvements.</p></div>
    <div class="service"><div class="icon"><svg width="60" height="60" viewBox="0 0 60 60"><circle cx="30" cy="12" r="6" fill="#fff"/><path d="M14 48h32M30 20v18M18 30l12 6 12-6" fill="none" stroke="#fff" stroke-width="4"/></svg></div><h4>MINDFULNESS AND YOGA<br>SESSIONS</h4><p>Join our yoga sessions to improve overall clarity and physical flexibility in a calming environment.</p></div>
  </div>
</section>

<section class="section testimonials center">
  <div class="eyebrow">OUR TESTIMONIALS</div>
  <h2 class="heading">CLIENT SUCCESS STORIES</h2>
  <div class="rule"></div>
  <div class="quote" style="left:100px;top:300px;width:290px"><div class="who"><div class="avatar" role="img" aria-label="Client portrait"></div><div><b>LENA HARTLEY</b><small>Busy mum</small></div></div><p>I love how the wellness programs fit into my hectic schedule. I feel healthier and more energised!</p></div>
  <div class="quote featured" style="left:418px;top:280px;width:360px;height:210px"><div class="who"><div class="avatar" role="img" aria-label="Client portrait"></div><div><b>NORA WHITFIELD</b><small>Fitness Enthusiast</small></div></div><p>The Wellness Barn has completely changed my approach to fitness. Their programs are tailored and effective!</p></div>
  <div class="quote" style="left:806px;top:300px;width:294px"><div class="who"><div class="avatar" role="img" aria-label="Client portrait"></div><div><b>OWEN CALDWELL</b><small>Retired Teacher</small></div></div><p>I never thought I could regain my mobility. The physiotherapy classes were a game changer!</p></div>
</section>

<section class="section team on-green center">
  <svg class="edge" style="top:-1px" height="30" viewBox="0 0 1200 30" preserveAspectRatio="none"><path d="M0 0H1200V14L1130 24 1060 10 990 22 920 12 850 26 780 12 710 22 640 10 570 24 500 12 430 22 360 10 290 24 220 12 150 22 80 10 0 20Z" fill="#e6d7b3"/></svg>
  <div class="eyebrow">MEET OUR TEAM</div>
  <h2 class="heading">GET TO KNOW US</h2>
  <div class="rule"></div>
  <div class="placeholder team-photo" role="img" aria-label="Portrait of the lead physiotherapist in a clinic"></div>
  <div class="member"><h3>DR. CLARA BENSON</h3><small>Lead Physiotherapist</small><p>Dr. Clara specialises in sports rehabilitation and has over 15 years of experience in helping clients recover from injuries.</p><span class="btn">VIEW MORE</span></div>
  <svg class="edge" style="bottom:-1px" height="30" viewBox="0 0 1200 30" preserveAspectRatio="none"><path d="M0 30H1200V14L1120 4 1050 18 980 6 910 20 840 8 770 18 700 4 630 16 560 6 490 20 420 8 350 18 280 4 210 16 140 6 70 20 0 10Z" fill="#efe3c6"/></svg>
</section>

<section class="section faq center">
  <div class="eyebrow">FAQS</div>
  <h2 class="heading">ANY QUESTIONS</h2>
  <div class="rule"></div>
  <p class="intro">Find answers to common questions about our health and wellness programs, services, and how we can support your journey to better health.</p>
  <div class="faq-list">
    <div class="faq-item"><span>What types of programs do you offer?</span><span>+</span></div>
    <div class="faq-item"><span>How can I get started?</span><span>+</span></div>
    <div class="faq-item"><span>Are your classes suitable for beginners?</span><span>+</span></div>
  </div>
  <span class="btn">VIEW PROGRAMS</span>
</section>

<footer class="section footer">
  <div class="logo"><span class="logo-dot"></span><span class="logo-name">THE WELLNESS BARN</span></div>
  <nav class="footer-nav"><a>HOME</a><a>SHOP</a><a>ABOUT US</a><a>PROGRAMS</a><a>TESTIMONIALS</a><a>CONTACT US</a></nav>
  <div class="cols">
    <div class="col"><h5>EMAIL US</h5>For inquiries or more information, feel free to reach out via email at hello@wellnessbarn.example. We are here to assist you with any questions you may have.</div>
    <div class="col"><h5>CALL US</h5>You can contact us directly at +61 7 5550 0142. Our team is available to take your calls and provide support during business hours.</div>
    <div class="col"><h5>VISIT US</h5>We are located at 45 Timber Lane, Greenvale, Australia, 4000. Come visit us to learn more about our programs and how we can help you achieve your health goals.</div>
  </div>
  <div class="copy">Copyright 2025 All Rights Reserved</div>
</footer>

</body>
</html>
```